Dalvick's Business Card

I need some designs for a new business card including the new logo attached. An old example of our business card is also attached to show all the data that should be included on the new design.
**I added some more examples someone had mocked up**

Contact Information for Business Card

Should include all info on other examples uploaded.

```html
<!DOCTYPE html>
<html lang="en">
<head>
<meta charset="utf-8">
<title>Dalvick's Business Card</title>
<link href="https://fonts.googleapis.com/css2?family=Montserrat:wght@400;500;600;700&display=swap" rel="stylesheet">
<style>
  :root {
    --canvas: #adadad;
    --brand-blue: #0870bb;
    --brand-blue-deep: #0a63a8;
    --brand-red: #e3262b;
    --paper: #ffffff;
    --ink: #4a4a4a;
    --rule: #8a8a8a;
  }
  * { margin: 0; padding: 0; box-sizing: border-box; }
  html, body { width: 1200px; height: 1000px; overflow: hidden; }
  body {
    background: var(--canvas);
    font-family: "Montserrat", sans-serif;
    position: relative;
  }
  .card {
    position: absolute;
    left: 294px;
    width: 613px;
    height: 351px;
    border-radius: 22px;
    overflow: hidden;
  }
  .card-front { top: 92px; }
  .card-back { top: 539px; background: var(--paper); }

  .front-pattern {
    position: absolute; inset: 0;
    background: linear-gradient(100deg, #2f86c8 0%, var(--brand-blue) 45%, var(--brand-blue-deep) 100%);
  }
  .wordmark {
    position: absolute;
    display: flex;
    align-items: center;
    gap: 10px;
    font-weight: 700;
    font-size: 36px;
    letter-spacing: 0.5px;
    line-height: 1;
  }
  .wordmark .dot {
    width: 40px; height: 40px; border-radius: 50%;
    flex: none;
  }
  .wordmark-front { left: 290px; top: 221px; color: var(--paper); }
  .wordmark-front .dot { background: var(--paper); }
  .wordmark-back { left: 172px; top: 60px; color: var(--brand-blue); }
  .wordmark-back .dot { background: var(--brand-red); }

  .person {
    position: absolute;
    top: 173px; left: 0; right: 0;
    display: flex;
    justify-content: center;
    align-items: center;
  }
  .person-name {
    font-size: 23px;
    font-weight: 500;
    color: var(--brand-blue);
    padding-right: 15px;
  }
  .person-contact {
    border-left: 2px solid var(--rule);
    padding-left: 10px;
    height: 48px;
    display: flex; flex-direction: column; justify-content: center; gap: 2px;
    font-size: 15.5px;
    color: var(--ink);
  }
  .contact-line { display: flex; align-items: center; gap: 7px; }
  .contact-line svg { width: 12px; height: 12px; fill: var(--brand-red); flex: none; }
  .address {
    position: absolute;
    bottom: 22px; left: 0; right: 0;
    text-align: center;
    font-size: 13.5px;
    color: var(--ink);
  }
</style>
</head>
<body>
  <section class="card card-front">
    <div class="front-pattern" role="img" aria-label="Repeating faint brand pattern on blue background"></div>
    <div class="wordmark wordmark-front"><span class="dot"></span><span>DALVICK'S</span></div>
  </section>

  <section class="card card-back">
    <div class="wordmark wordmark-back"><span class="dot"></span><span>DALVICK'S</span></div>
    <div class="person">
      <div class="person-name">Reid Dalvick</div>
      <div class="person-contact">
        <div class="contact-line">
          <svg viewBox="0 0 24 24" aria-hidden="true"><path d="M6.6 10.8a15.1 15.1 0 0 0 6.6 6.6l2.2-2.2a1 1 0 0 1 1-.25 11.4 11.4 0 0 0 3.6.57 1 1 0 0 1 1 1V20a1 1 0 0 1-1 1A17 17 0 0 1 3 4a1 1 0 0 1 1-1h3.5a1 1 0 0 1 1 1c0 1.25.2 2.45.57 3.57a1 1 0 0 1-.25 1z"/></svg>
          <span>555.014.2738</span>
        </div>
        <div class="contact-line">
          <svg viewBox="0 0 24 24" aria-hidden="true"><path d="M2 5h20v14H2z M2 5l10 8 10-8" /><path d="M3 6l9 7 9-7" fill="#fff"/></svg>
          <span>hvacdalvick@mailbox.com</span>
        </div>
      </div>
    </div>
    <div class="address">418 Maple Ridge Road, Fairview, IA 50000, EUA</div>
  </section>
</body>
</html>
```